Website design for lighting products company

We want a design for our website. The website is for a company that sells lighting products. The structure is similar to the below website. We really like their design as well: www.palvenorlighting.com

Industry/Entity Type

Lighting

Number of Pages Required

5+ page

Colors

Designer to choose colors to be used in the design.

Requirements
Must have
• Simple design

```html
<!DOCTYPE html>
<html lang="en">
<head>
<meta charset="utf-8">
<title>Lumora Lighting</title>
<link href="https://fonts.googleapis.com/css2?family=Roboto:wght@400;500;700;900&family=Open+Sans:wght@400;600&display=swap" rel="stylesheet">
<style>
:root{
  --blue:#1d64c2;
  --blue-dark:#0b1a45;
  --navy:#070f2e;
  --ink:#2c2c2c;
  --body:#555;
  --light:#f2f3f5;
  --white:#fff;
  --footer:#ececec;
  --nav-active:#4f9cf0;
}
*{box-sizing:border-box;margin:0;padding:0}
html,body{width:1200px;height:3917px;overflow:hidden;background:var(--white)}
body{font-family:"Open Sans",sans-serif;color:var(--body)}
.page{position:relative;width:1200px;height:3917px}
.abs{position:absolute}
.center{left:0;width:1200px;text-align:center}

/* hero */
.hero{left:0;top:0;width:1200px;height:703px;background:
  radial-gradient(ellipse at 70% 25%,#5a3fbf 0%,rgba(60,40,150,0) 45%),
  radial-gradient(ellipse at 30% 80%,#b2562a 0%,rgba(120,50,30,0) 50%),
  linear-gradient(180deg,#1a1550 0%,#2a1d5e 40%,#4a2a2a 75%,#3a1a20 100%)}
.hero-shade{left:0;top:0;width:1200px;height:703px;background:rgba(10,10,30,.25)}
.brand{font-family:"Roboto",sans-serif;font-weight:700;color:var(--white);font-size:30px;display:flex;align-items:center;gap:10px}
.brand-dot{width:22px;height:22px;border-radius:50%;background:currentColor}
.call{left:613px;top:30px;display:flex;align-items:center;gap:10px;color:var(--white);font-family:"Roboto",sans-serif;font-weight:500;font-size:18px;line-height:21px}
.search{left:833px;top:33px;width:221px;height:39px;border-radius:20px;background:var(--white);font-size:12px;color:#555;padding:11px 16px;display:flex;justify-content:space-between}
.nav{top:98px;font-family:"Roboto",sans-serif;font-weight:500;font-size:16px;color:var(--white)}
.nav.active{color:var(--nav-active)}
.play{left:565px;top:262px}
.hero-title{top:360px;font-family:"Roboto",sans-serif;font-weight:900;font-size:78px;color:var(--white);letter-spacing:1px}
.hero-sub{top:454px;font-family:"Roboto",sans-serif;font-weight:700;font-size:23px;line-height:41px;color:var(--white);letter-spacing:.5px}
.dots{left:564px;top:622px;display:flex;gap:8px}
.dots span{width:18px;height:18px;border-radius:50%;border:2px solid var(--white)}
.dots span.on{background:var(--white)}

/* headings */
.h2{font-family:"Roboto",sans-serif;font-weight:500;font-size:38px;color:var(--ink)}
.rule{left:566px;width:68px;height:3px;background:var(--blue)}

/* welcome */
.welcome{left:0;top:703px;width:1200px;height:465px;background:linear-gradient(180deg,#e9eaec 0%,#fafafa 45%,#eeeff1 100%)}
.welcome-text{left:158px;top:872px;width:884px;text-align:center;font-size:17px;line-height:32px;color:#555}
.btn{font-family:"Roboto",sans-serif;font-weight:500;font-size:14px;display:flex;align-items:center;justify-content:center;border-radius:3px}
.btn-solid{background:var(--blue);color:var(--white);box-shadow:0 3px 6px rgba(0,0,0,.2)}
.btn-line{border:2px solid var(--white);color:var(--white)}

/* services */
.services{left:0;top:1168px;width:1200px;height:709px;background:radial-gradient(ellipse at 50% 40%,#132a6a 0%,#0a1742 45%,var(--navy) 100%)}
.service{border:2px solid var(--white);border-radius:8px;display:flex;flex-direction:column;align-items:center;justify-content:flex-end;padding-bottom:22px;color:var(--white);font-family:"Roboto",sans-serif;font-weight:500;font-size:19px}
.service svg{margin-bottom:16px}
.service-feature{left:443px;top:1393px;width:314px;height:384px;background:var(--blue);border-radius:4px;color:var(--white);text-align:center;padding-top:22px}
.service-feature h3{font-family:"Roboto",sans-serif;font-weight:500;font-size:24px;margin-top:14px}
.service-feature p{font-family:"Roboto",sans-serif;font-size:14px;line-height:26px;margin:10px 22px 0}

/* products */
.card{width:235px;height:282px;border:1px solid #ddd;background:#f4f4f4;box-shadow:0 2px 4px rgba(0,0,0,.08)}
.card-img{width:100%;height:200px;background:var(--white)}
.card p{font-family:"Roboto",sans-serif;font-size:16px;line-height:26px;color:#444;text-align:center;margin-top:14px}

/* gallery */
.tile{height:327px}

/* newsletter */
.newsletter{left:0;top:3126px;width:1200px;height:319px;background:linear-gradient(180deg,#f6f6f7,#eeeff1)}
.news-text{top:3244px;font-size:15px;line-height:26px;color:#444}
.email{left:329px;top:3325px;width:390px;height:37px;background:var(--white);box-shadow:0 1px 4px rgba(0,0,0,.15);font-size:12px;color:#555;padding:11px 18px}

/* footer */
.footer{left:0;top:3445px;width:1200px;height:365px;background:var(--footer)}
.foot-brand{left:156px;top:3585px;color:#1c2b5a;font-size:32px}
.social{left:159px;top:3640px;display:flex;gap:5px}
.social span{width:28px;height:28px;border-radius:50%;border:1.5px solid #333}
.foot-h{font-family:"Roboto",sans-serif;font-size:26px;color:#222}
.foot-item{font-size:15px;line-height:21px;color:#333}
.foot-links{font-size:15px;line-height:32px;color:#333}
.legal{top:3848px;font-size:15px;color:#333}
</style>
</head>
<body>
<div class="page">

  <!-- hero -->
  <div class="abs hero" role="img" aria-label="Night photo of a modern building with a colourful illuminated glass canopy"></div>
  <div class="abs hero-shade"></div>
  <div class="abs brand" style="left:150px;top:60px"><span class="brand-dot"></span>Lumora Lighting</div>
  <div class="abs call">
    <svg width="38" height="38" viewBox="0 0 38 38"><circle cx="19" cy="19" r="17" fill="none" stroke="#fff" stroke-width="2"/><path d="M13 11c1-1 2-1 3 0l2 3c.5 1 0 2-1 2.5 1 2 2.5 3.5 4.5 4.5.5-1 1.5-1.5 2.5-1l3 2c1 1 1 2 0 3-2 2-4 2-7 0-3-2-5-4-7-7-2-3-2-5 0-7z" fill="#fff"/></svg>
    <div>Call Us<br>(555) 0142-7788</div>
  </div>
  <div class="abs search"><span>Search</span>
    <svg width="12" height="12" viewBox="0 0 12 12"><circle cx="5" cy="5" r="3.5" fill="none" stroke="#555" stroke-width="1.5"/><path d="M8 8l3 3" stroke="#555" stroke-width="1.5"/></svg></div>
  <div class="abs nav active" style="left:368px">HOME</div>
  <div class="abs nav" style="left:455px">ABOUT US</div>
  <div class="abs nav" style="left:576px">SERVICES</div>
  <div class="abs nav" style="left:695px">PRODUCTS</div>
  <div class="abs nav" style="left:823px">MAINTENANCE</div>
  <div class="abs nav" style="left:981px">CONTACT</div>
  <svg class="abs play" width="70" height="70" viewBox="0 0 70 70"><circle cx="35" cy="35" r="33" fill="none" stroke="#fff" stroke-width="2.5"/><path d="M28 22l18 13-18 13z" fill="none" stroke="#fff" stroke-width="2.5"/></svg>
  <div class="abs center hero-title">LUMORA LIGHTING</div>
  <div class="abs center hero-sub">ONE OF THE UK’S LARGEST MANUFACTURERS OF<br>COMMERCIAL LIGHTING SOLUTIONS</div>
  <div class="abs dots"><span class="on"></span><span></span><span></span></div>

  <!-- welcome -->
  <div class="abs welcome" role="img" aria-label="Bright empty white interior room"></div>
  <div class="abs center h2" style="top:780px">WELCOME TO LUMORA LIGHTING</div>
  <div class="abs rule" style="top:833px"></div>
  <p class="abs welcome-text">Sed ut perspiciatis unde omnis iste natus error sit voluptatem accusantium doloremque laudantium, totam rem aperiam, eaque ipsa quae ab illo inventore veritatis et quasi architecto beatae vitae dicta sunt explicabo. Nemo enim ipsam voluptatem quia voluptas sit aspernatur aut odit aut fugit, sed quia consequuntur magni dolores eos qui ratione voluptatem sequi nesciunt. Neque porro quisquam est, qui dolorem ipsum quia dolor sit amet, consectetur, adipisci velit, sed quia non numquam eius modi tempora incidunt ut labore et dolore magnam</p>
  <div class="abs btn btn-solid" style="left:532px;top:1065px;width:137px;height:41px">READ MORE</div>

  <!-- services -->
  <div class="abs services" role="img" aria-label="Dark blue abstract background with glowing light lines"></div>
  <div class="abs center h2" style="top:1264px;color:#fff;font-weight:700">OUR SERVICES</div>
  <div class="abs rule" style="top:1336px;background:#fff"></div>

  <div class="abs service" style="left:170px;top:1393px;width:228px;height:175px">
    <svg width="76" height="82" viewBox="0 0 76 82" fill="none" stroke="#3d8ff5" stroke-width="3"><rect x="6" y="26" width="30" height="54"/><rect x="36" y="10" width="32" height="70"/><path d="M44 10V2h16v8M12 34h6M24 34h6M12 46h6M24 46h6M12 58h6M24 58h6M44 22h6M56 22h6M44 34h6M56 34h6M44 46v26M52 46v26M60 46v26"/></svg>
    INDOOR</div>
  <div class="abs service" style="left:170px;top:1602px;width:228px;height:175px">
    <svg width="84" height="80" viewBox="0 0 84 80" fill="none" stroke="#fff" stroke-width="3"><path d="M10 8l64 64M74 8L10 72M6 4l14 4-4 10-12-4zM78 4l-14 4 4 10 12-4zM32 60l-8 14M52 60l8 14"/></svg>
    LIGHTING CONTROLS</div>
  <div class="abs service-feature">
    <svg width="100" height="96" viewBox="0 0 100 96" fill="none" stroke="#fff" stroke-width="3"><rect x="6" y="44" width="22" height="50"/><rect x="28" y="18" width="22" height="76"/><rect x="50" y="4" width="20" height="90"/><rect x="70" y="34" width="24" height="60"/><path d="M12 54h10M12 66h10M34 28h10M34 40h10M34 52h10M56 14h8M56 26h8M56 38h8M76 44h12M76 56h12M0 94h100"/></svg>
    <h3>OUTDOOR</h3>
    <p>Lorem ipsum dolor sit amet, consectetur adipiscing elit, sed do eiusmod tempor incididunt ut labore et dolore magna aliqua. Ut enim ad minim</p>
    <div class="btn btn-line" style="margin:20px auto 0;width:128px;height:40px">READ MORE</div>
  </div>
  <div class="abs service" style="left:803px;top:1393px;width:227px;height:175px">
    <svg width="84" height="84" viewBox="0 0 84 84" fill="none" stroke="#fff" stroke-width="3"><circle cx="22" cy="18" r="15"/><circle cx="62" cy="18" r="15"/><path d="M22 18l6-8M62 18l6-8"/><rect x="4" y="40" width="76" height="40" rx="3"/><circle cx="20" cy="64" r="5"/><circle cx="36" cy="64" r="5"/><rect x="52" y="50" width="18" height="22"/><path d="M56 57h10M56 64h10"/></svg>
    EMERGENCY LIGHTING</div>
  <div class="abs service" style="left:803px;top:1602px;width:227px;height:175px">
    <svg width="72" height="74" viewBox="0 0 72 74" fill="none" stroke="#fff" stroke-width="3"><rect x="2" y="2" width="68" height="14"/><rect x="2" y="20" width="68" height="52"/><rect x="14" y="36" width="44" height="20"/><path d="M28 36v20M44 36v20"/></svg>
    LATEST SOLUTIONS</div>

  <!-- products -->
  <div class="abs center h2" style="top:1948px;font-weight:700">OUR PRODUCTS</div>
  <div class="abs rule" style="top:2018px"></div>
  <div class="abs card" style="left:99px;top:2078px"><div class="card-img" role="img" aria-label="Product photo of a linear batten light fitting" style="background:linear-gradient(180deg,#fff,#eef0f2)"></div><p>Quis Autem Vel Eum Iure<br>Derit Qui In Ea Volup</p></div>
  <div class="abs card" style="left:354px;top:2078px"><div class="card-img" role="img" aria-label="Product photo of a multi-LED round floodlight" style="background:radial-gradient(circle at 50% 45%,#c9ccd0 0%,#8e9399 30%,#fff 55%)"></div><p>Quis Autem Vel Eum Iure<br>Derit Qui In Ea Volup</p></div>
  <div class="abs card" style="left:610px;top:2078px"><div class="card-img" role="img" aria-label="Product photo of a white surface-mounted downlight" style="background:radial-gradient(ellipse at 50% 50%,#e4e6e8 0%,#f4f5f6 35%,#fff 60%)"></div><p>Quis Autem Vel Eum Iure<br>Derit Qui In Ea Volup</p></div>
  <div class="abs card" style="left:866px;top:2078px"><div class="card-img" role="img" aria-label="Product photo of a square LED panel light" style="background:linear-gradient(180deg,#fff,#f2f3f4)"></div><p>Quis Autem Vel Eum Iure<br>Derit Qui In Ea Volup</p></div>

  <!-- gallery -->
  <div class="abs tile" style="left:0;top:2464px;width:392px;background:linear-gradient(160deg,#6a5a8a,#2a2a6e 55%,#3a7ae0)" role="img" aria-label="Ballroom interior with chandeliers and blue accent lighting"></div>
  <div class="abs tile" style="left:400px;top:2464px;width:400px;background:linear-gradient(160deg,#2d4a80,#1d3a75 60%,#12295c)" role="img" aria-label="Blue-tinted modern glass office building"></div>
  <div class="abs center" style="left:400px;width:400px;top:2572px;font-family:'Roboto',sans-serif;font-weight:700;font-size:42px;color:#fff">WORKSPACE</div>
  <div class="abs btn btn-line" style="left:481px;top:2645px;width:222px;height:38px;font-size:16px">VIEW MORE PRODUCTS</div>
  <div class="abs tile" style="left:808px;top:2464px;width:392px;background:linear-gradient(180deg,#d8d4cc,#c9b89a 55%,#e8e4dc)" role="img" aria-label="Bright hospital reception hall with ceiling lights"></div>
  <div class="abs tile" style="left:0;top:2799px;width:392px;background:linear-gradient(180deg,#8aa0c8,#e3e2df 40%,#f2f2f0)" role="img" aria-label="White bathroom with cove lighting"></div>
  <div class="abs tile" style="left:400px;top:2799px;width:400px;background:linear-gradient(180deg,#1c2540,#3a3f52 55%,#6f6a62)" role="img" aria-label="House exterior at night with lit garden steps"></div>
  <div class="abs tile" style="left:808px;top:2799px;width:392px;background:linear-gradient(180deg,#7f8fd0,#e6e2dc 35%,#b89a7a)" role="img" aria-label="Living and dining room with recessed ceiling lights"></div>

  <!-- newsletter -->
  <div class="abs newsletter"></div>
  <div class="abs center h2" style="top:3189px;font-weight:700;font-size:36px">SIGN UP TO OUR NEWSLETTER</div>
  <p class="abs center news-text">Sed ut perspiciatis unde omnis iste natus error sit voluptatem accusantium doloremque<br>laudantium, totam rem aperiam, eaque ipsa quae</p>
  <div class="abs email">Enter Email</div>
  <div class="abs btn" style="left:736px;top:3324px;width:136px;height:38px;background:#1b4fa8;color:#fff;font-size:15px">SUBSCRIBE</div>

  <!-- footer -->
  <div class="abs footer"></div>
  <div class="abs brand foot-brand"><span class="brand-dot" style="color:#2a6ee0"></span>Lumora</div>
  <div class="abs social"><span></span><span></span><span></span><span></span></div>

  <div class="abs foot-h" style="left:377px;top:3518px">Contact us</div>
  <svg class="abs" style="left:380px;top:3578px" width="14" height="20" viewBox="0 0 14 20"><path d="M7 0a7 7 0 0 1 7 7c0 5-7 13-7 13S0 12 0 7a7 7 0 0 1 7-7z" fill="#1d64c2"/><circle cx="7" cy="7" r="2.5" fill="#ececec"/></svg>
  <div class="abs foot-item" style="left:414px;top:3578px">Lumora Lighting<br>Kestrel Road, Harbourview, WA</div>
  <svg class="abs" style="left:379px;top:3626px" width="18" height="18" viewBox="0 0 18 18"><path d="M3 1c1-1 2-1 3 0l2 3c.5 1 0 2-1 2.5 1 2 2.5 3.5 4.5 4.5.5-1 1.5-1.5 2.5-1l3 2c1 1 1 2 0 3-2 2-4 2-7 0-3-2-5-4-7-7-2-3-2-5 0-7z" fill="#1d64c2"/></svg>
  <div class="abs foot-item" style="left:412px;top:3626px">Phone:<br>555 0198 3321</div>
  <svg class="abs" style="left:379px;top:3683px" width="18" height="14" viewBox="0 0 18 14"><rect width="18" height="14" rx="1" fill="#1d64c2"/><path d="M1 1l8 7 8-7" fill="none" stroke="#ececec" stroke-width="1.5"/></svg>
  <div class="abs foot-item" style="left:414px;top:3678px">Email:<br>info@lumoralighting.com</div>

  <div class="abs foot-h" style="left:664px;top:3516px">Quick links</div>
  <div class="abs foot-links" style="left:668px;top:3561px">Home<br>About Us<br>Our Services<br>Products<br>Blog<br>Contact Us</div>
  <div class="abs foot-h" style="left:856px;top:3516px">Useful Links</div>
  <div class="abs foot-links" style="left:859px;top:3561px">Terms &amp; Conditions<br>Privacy policy<br>Warranty<br>Terms of use<br>Environment<br>Quality Policy</div>

  <div class="abs center legal">Lumora Lighting © 2019 All Rights Reserved | Privacy Policy | Terms and Conditions</div>
</div>
</body>
</html>
```